The Lark Whiskey & Coffee - Bar Menu

The Lark is a speakeasy style coffee and whiskey bar. Upscale with design elements tying in both prohibition era elegance and modern touches.

Black and Gold are our colors. (see logo)

We would need a 8 page menu- front and back. 4.24 in x 11 in for each page. The pages would be:

Intro page
Food/Dessert
Cocktails x 2 pages
Wine- Glass Pour
Wine- Bottle only
Beer
Non-Alcoholic Beverages

Attached is the menu cocktails and food/non alcoholic.

We need an editable format as this menu would be constantly changing.

UPDATE: The owner would potentially like to see the use of the original floor plans incorporated into the menu design. I have uploaded those to this brief.

UPDATE: I have added some photos that show the style the owner would like the writing to be displayed.

Requirements
Should not have
• No pictures of wine or beer or other images. Clipart could be fine, but we want to showcase class and an upscale vibe.

```html
<!DOCTYPE html>
<html lang="en">
<head>
<meta charset="utf-8">
<title>The Lark Whiskey &amp; Coffee – Bar Menu</title>
<link href="https://fonts.googleapis.com/css2?family=Poiret+One&display=swap" rel="stylesheet">
<style>
  :root {
    --paper: #ffffff;
    --ink: #1c1b1f;
    --gold: #d9ab4f;
    --gold-soft: #b98d3c;
  }
  * { margin: 0; padding: 0; box-sizing: border-box; }
  html, body { width: 1200px; height: 754px; overflow: hidden; background: var(--paper); }
  body { position: relative; font-family: "Poiret One", sans-serif; color: var(--gold); }

  .page { position: absolute; top: 34px; width: 268px; height: 697px; background: var(--ink); }
  .page--intro { left: 24.5px; }
  .page--food { left: 320px; }
  .page--cocktails-a { left: 615px; }
  .page--cocktails-b { left: 910.5px; }

  .page svg.rules { position: absolute; inset: 0; width: 268px; height: 697px; }

  /* Intro page */
  .brand { position: absolute; left: 0; width: 268px; text-align: center; }
  .brand__mark { position: absolute; top: 72px; left: 118px; width: 32px; height: 32px; background: var(--gold); }
  .brand__name { top: 152px; font-size: 36px; letter-spacing: 3px; line-height: 40px; }
  .brand__sub { top: 194px; font-size: 11.5px; letter-spacing: 2px; }
  .pattern-field {
    position: absolute; left: 28px; top: 216px; width: 212px; height: 452px;
    background: linear-gradient(180deg, #2a2620 0%, #6b5327 45%, #8f6f33 70%, #4a3b22 100%);
  }
  .address {
    position: absolute; left: 50px; top: 568px; width: 168px; height: 56px;
    background: var(--ink); border: 1px solid var(--gold); outline: 1px solid var(--gold); outline-offset: 3px;
    display: flex; flex-direction: column; justify-content: center; text-align: center;
    font-size: 14px; line-height: 17px;
  }

  /* Menu items */
  .label { position: absolute; font-size: 11.5px; letter-spacing: 0.2px; }
  .item { position: absolute; width: 250px; }
  .item h3 { font-weight: 400; font-size: 11px; line-height: 13px; letter-spacing: -0.2px; }
  .item p { font-size: 9.4px; line-height: 11.5px; letter-spacing: -0.2px; margin-top: 0; }
  .price { position: absolute; right: 8px; font-size: 9.5px; }

  .page--food .item { left: 104px; width: 160px; }
  .page--cocktails-a .item, .page--cocktails-b .item { left: 105px; width: 160px; }

  .dessert {
    position: absolute; left: 10px; top: 572px; width: 250px; height: 105px;
    border: 1px solid var(--gold); text-align: center;
  }
  .dessert h2 {
    position: absolute; top: -11px; left: 50%; transform: translateX(-50%);
    background: var(--ink); padding: 0 3px; font-weight: 400; font-size: 18px; line-height: 20px;
  }
  .dessert .treat { margin-top: 16px; }
  .dessert .treat + .treat { margin-top: 8px; }
  .dessert h3 { font-weight: 400; font-size: 11px; line-height: 13px; }
  .dessert p { font-size: 9.4px; line-height: 11.5px; }
</style>
</head>
<body>

<section class="page page--intro" aria-label="Cover">
  <svg class="rules" viewBox="0 0 268 697" aria-hidden="true">
    <g fill="none" stroke="var(--gold)" stroke-width="1">
      <path d="M28 16 H240 V26 H250 V36 H259 V661 H250 V671 H240 V681 H28 V671 H18 V661 H9 V36 H18 V26 H28 Z"/>
      <path d="M36 25 H232 V34 H241 V44 H250 V653 H241 V663 H232 V672 H36 V663 H27 V653 H18 V44 H27 V34 H36 Z"/>
    </g>
  </svg>
  <div class="pattern-field" role="img" aria-label="Art deco arch pattern with a gabled building ornament, lotus flourishes and wave lines in gold"></div>
  <span class="brand__mark" aria-hidden="true"></span>
  <h1 class="brand brand__name" style="font-weight:400">THE LARK</h1>
  <p class="brand brand__sub">WHISKEY &amp; COFFEE</p>
  <address class="address" style="font-style:normal">
    <span>Calloway Building</span>
    <span>Marston, WA 98210</span>
  </address>
</section>

<section class="page page--food" aria-label="Food">
  <svg class="rules" viewBox="0 0 268 697" aria-hidden="true">
    <text x="91" y="66" transform="rotate(-90 91 66)" fill="var(--gold)" font-family="Poiret One, sans-serif" font-size="18" letter-spacing="1">FOOD</text>
    <line x1="83.5" y1="72" x2="83.5" y2="530" stroke="var(--gold)" stroke-width="1"/>
  </svg>
  <div class="item" style="top:17px"><h3>BONE MARROW</h3><p>BONE MARROW ROASTED<br>WITH SEA SALT AND SERVED<br>WITH WARM TORTILLAS</p></div>
  <span class="price" style="top:19px">$20</span>
  <div class="item" style="top:113px"><h3>CHARCUTERIE BOARD</h3><p>ASSORTED ARTISAN MEATS<br>AND CHEESES, NUTS, AND<br>FRUITS</p></div>
  <span class="price" style="top:115px">$25</span>
  <div class="item" style="top:209px"><h3>HUMMUS, VEGGIES &amp; PITA</h3><p>ASSORTED VEGETABLES WITH<br>WARM PITA AND ROASTED<br>GARLIC HUMMUS</p></div>
  <span class="price" style="top:211px">$16</span>
  <div class="item" style="top:305px"><h3>LAMB CHOPS</h3><p>LAMB CHOPS BROILED<br>WITH ROSEMARY</p></div>
  <span class="price" style="top:307px">$18</span>
  <div class="item" style="top:389px"><h3>TUNA TOWER</h3><p>FRESH TUNA SERVED WITH<br>WHITE RICE, AVOCADO<br>AND SPICES</p></div>
  <span class="price" style="top:391px">$17</span>
  <div class="item" style="top:485px"><h3>LETTUCE WRAP-WALNUT SHRIMP</h3><p>HONEY WALNUT AIOLI COATED<br>SHRIMP AND LETTUCE CUPS WITH<br>A CANDIED WALNUT</p></div>
  <span class="price" style="top:487px">$13</span>

  <div class="dessert">
    <h2>DESSERT</h2>
    <div class="treat"><h3>TART</h3><p>YOUR CHOICE OF APPLE OR BERRY<br>WITH VANILLA ICE CREAM</p></div>
    <div class="treat"><h3>CHEESECAKE</h3><p>CHOCOLATE OR<br>STRAWBERRY DRIZZLE</p></div>
  </div>
</section>

<section class="page page--cocktails-a" aria-label="Cocktails">
  <svg class="rules" viewBox="0 0 268 697" aria-hidden="true">
    <text x="93" y="108" transform="rotate(-90 93 108)" fill="var(--gold)" font-family="Poiret One, sans-serif" font-size="21" letter-spacing="0">COCKTAILS</text>
    <line x1="84" y1="114" x2="84" y2="675" stroke="var(--gold)" stroke-width="1"/>
  </svg>
  <span class="label" style="left:18px; top:18px">WHISKEY</span>
  <span class="label" style="left:43px; top:434px">GIN</span>
  <div class="item" style="top:17px"><h3>THE DARK WALNUT</h3><p>IRISH WHISKEY, WALNUT LIQUEUR,<br>AGAVE NECTAR, EXPRESSO</p></div>
  <div class="item" style="top:80px"><h3>PENICILLIN*</h3><p>KD BLACK, LARROWMORE, LEMON<br>JUICE, GINGER, HONEY SYRUP<br>(R)(CANDIED GINGER GARNISH)</p></div>
  <div class="item" style="top:157px"><h3>ALBERT HADLEY (LOCAL BOOTLEGGER)</h3><p>OLD FENWICK, HONEY LIQUEUR,<br>LEMON JUICE, HABANERO BITTERS</p></div>
  <div class="item" style="top:221px"><h3>RUTHERFORD** (NY SOUR)</h3><p>BOURBON, DEMERARA SIMPLE SYRUP,<br>LEMON JUICE, RED WINE FLOAT</p></div>
  <div class="item" style="top:287px"><h3>DECADENCE</h3><p>BLENDED SCOTCH/WHISKEY, SWEET<br>SHERRY, DRY SHERRY, CHOCOLATE<br>BITTERS, ORANGE, RASPBERRY</p></div>
  <div class="item" style="top:363px"><h3>GOLD RUSH**</h3><p>BOURBON, HONEY SYRUP, AMARO,<br>LEMON JUICE (EGGWHITE)</p></div>
  <div class="item" style="top:428px"><h3>CLOVER CLUB*</h3><p>AZURINE GIN, RASPERRY LIQUOR,<br>LEMON JUICE, RASPBERRIES, VANILLA,<br>PROSECCO, MILK (CLARIFIED)</p></div>
  <div class="item" style="top:502px"><h3>CLOVER CLUB#2**</h3><p>GIN, MAISON RIVEL VERMOUTH,<br>RASPBERRY, LEMON JUICE, EGGWHITE</p></div>
  <div class="item" style="top:565px"><h3>LIMONATA</h3><p>GIN (LEMON INFUSED), LIMONCELLO,<br>LEMON CURD, LEMON JUICE, SANTA<br>LUCIA</p></div>
  <div class="item" style="top:640px"><h3>COLONY COCKTAIL</h3><p>GIN, PINK GRAPEFRUIT, MARASCHINO<br>LIQUEUR, GRAPEFRUIT TWIST</p></div>
</section>

<section class="page page--cocktails-b" aria-label="Cocktails continued">
  <svg class="rules" viewBox="0 0 268 697" aria-hidden="true">
    <text x="93" y="108" transform="rotate(-90 93 108)" fill="var(--gold)" font-family="Poiret One, sans-serif" font-size="21" letter-spacing="0">COCKTAILS</text>
    <line x1="84" y1="114" x2="84" y2="675" stroke="var(--gold)" stroke-width="1"/>
  </svg>
  <span class="label" style="left:22px; top:18px">VODKA</span>
  <span class="label" style="left:20px; top:181px">TEQUILA</span>
  <span class="label" style="left:40px; top:342px">RUM</span>
  <span class="label" style="left:11px; top:553px">CORDIALS</span>
  <div class="item" style="top:17px"><h3>THE AFFAIR</h3><p>VODKA (STRAWBERRY/ORANGE<br>INFUSION), LEMON OLEO<br>SACCAHRUM, PEAFLOWER GIN<br>FLOAT (BLUE) (N&amp;N)</p></div>
  <div class="item" style="top:104px"><h3>BOOTLEGGERS GOLD</h3><p>VODKA, YELLOW CHANTEREL,<br>PINEAPPLE, LIME JUICE, SIMPLE SYRUP,<br>LEMON ZEST</p></div>
  <div class="item" style="top:181px"><h3>THE MAYAN</h3><p>DON RAMIRO BLANCO, RAICILLA<br>(NON-PEATY MEZCAL), GREEN<br>CHANTEREL, PISTACHIO LIQUEUR,<br>OLIVE, LIME</p></div>
  <div class="item" style="top:267px"><h3>TOREADOR*</h3><p>BLANCO, MEZCAL, APRICOT<br>CORDIAL, LIME JUICE, GRAPEFRUIT OIL<br>(OLEO), MEZCAL MIST</p></div>
  <div class="item" style="top:343px"><h3>SMUGGLERS COVE**</h3><p>RUM (CUBAN), POMEGRANITE LIQUEUR,<br>LEMON JUICE, MACADAMIA ORGEAT,<br>COCOA BITTERS (EGGWHITE)</p></div>
  <div class="item" style="top:418px"><h3>MARY ASHFORD*</h3><p>RUM (BLANCO CUBAN), PINEAPPLE,<br>MARASCHINO LIQUEUR, GRENADINE</p></div>
  <div class="item" style="top:481px"><h3>ROY RUM RUNNER (LOCAL)</h3><p>RUM (BLANCO), RHUM AGRICOLE<br>(NON-PEAT MEZCAL) LIME JUICE,<br>SIMPLE SYRUP W/IN SEASON FRUIT</p></div>
  <div class="item" style="top:555px"><h3>THE WAX POET</h3><p>COGNAC, BEESWAX, TOASTED<br>ALMOND LIQUEUR, MARIGOLD<br>LIQUEUR, LIME</p></div>
  <div class="item" style="top:630px"><h3>THE BOHEMIAN</h3><p>COGNAC, BROWN BUTTER, DARK<br>RUM, ORANGE LIQUEUR, PEAR<br>LIQUEUR, BITTERS</p></div>
</section>

</body>
</html>
```